Template Flyer- Corewell Stretch & Flow

I am wanting a template 1 page flyer designed to use on the back ground of newsletter (faded background) and for our advertising posters in A4, A3, for Facebook and Instagram compatibility.

I have loaded an example from another Studio called Pinegrove (file 3)- each time they have a new workshop to advertise a picture is placed in the little circle (so this is something I would want to do too where I can load a new picture each time a new workshop is running)- They have used the flyer like a water mark...I like this.

Our colour palette is what is on our logos and you can also visit our website for a feel for what we like www.corewellstretch.com.au

I need some of the designs edited a bit more and because of the time difference, there seems to be a 24hour period where we communicate with each other. May I please request another 2 days extension

Requirements
Must have
• Id like to have a picture in the back ground. My favourite back ground that has been produced so far is a background of both picture file 9 and 10 in either.
Nice to have
• 3 picture circles options to advertise the events/workshops I have each year.
• Brush stroke style circles (see picture attached)rather then smooth circles for the picture area (in a grey tone)
Should not have
• No BLACK colour writing or black circles

```html
<!DOCTYPE html>
<html lang="en">
<head>
<meta charset="UTF-8">
<title>Yoga &amp; Pilates Workshop, Ashford</title>
<link rel="stylesheet" href="https://fonts.googleapis.com/css2?family=Comfortaa:wght@600;700&family=Source+Sans+3:wght@600;700&display=swap">
<style>
  :root {
    --teal: #1a8aaa;
    --taupe: #b7ada0;
    --slate: #4a5156;
    --paper: #e9e8e6;
    --bg-warm: #d9d6d1;
    --bg-cool: #c9cbc6;
    --bg-green: #bcc2b6;
    --mat: #3a3836;
    --wood: #cfc7bb;
  }
  * { margin: 0; padding: 0; box-sizing: border-box; }
  html, body { width: 960px; height: 1200px; overflow: hidden; background: var(--paper); }
  .flyer {
    position: relative;
    width: 960px;
    height: 1200px;
    overflow: hidden;
    font-family: "Source Sans 3", "Source Sans Pro", sans-serif;
    text-align: center;
  }
  .backdrop {
    position: absolute; inset: 0;
    background:
      radial-gradient(ellipse at 85% 40%, var(--bg-green) 0%, transparent 55%),
      radial-gradient(ellipse at 15% 35%, var(--bg-warm) 0%, transparent 60%),
      linear-gradient(180deg, var(--paper) 0%, var(--bg-cool) 55%, var(--bg-warm) 100%);
  }
  .artwork { position: absolute; inset: 0; }
  .title {
    position: absolute; left: 0; right: 0; top: 22px;
    font-family: "Comfortaa", sans-serif;
    font-weight: 700;
    color: var(--teal);
    font-size: 56px;
    line-height: 76px;
    letter-spacing: -1px;
  }
  .title span { display: block; }
  .title .line-two { padding-left: 12px; }
  .details { position: absolute; left: 0; right: 0; top: 740px; color: var(--slate); }
  .date { color: var(--teal); font-size: 28px; font-weight: 700; line-height: 36px; }
  .date sup { font-size: 16px; line-height: 0; vertical-align: 0.7em; }
  .time { font-size: 21px; font-weight: 700; line-height: 30px; margin-top: 4px; }
  .venue { font-size: 21px; font-weight: 700; line-height: 25px; margin-top: 16px; }
  .investment-label { color: var(--teal); font-size: 29px; font-weight: 700; line-height: 36px; margin-top: 22px; }
  .price { font-size: 21px; font-weight: 700; line-height: 26px; margin-top: 17px; }
  .booking { color: var(--teal); font-size: 28px; font-weight: 700; line-height: 36px; margin-top: 23px; }
  .brand {
    position: absolute; left: 0; right: 0; top: 1110px;
    display: flex; justify-content: center; align-items: center; gap: 14px;
  }
  .brand-dot { width: 40px; height: 40px; border-radius: 50%; background: var(--teal); }
  .brand-name { font-size: 34px; font-weight: 600; color: var(--slate); }
  .tagline { position: absolute; left: 0; right: 0; top: 1160px; font-size: 13px; letter-spacing: 2px; color: var(--slate); font-weight: 600; padding-left: 60px; }
</style>
</head>
<body>
  <main class="flyer">
    <div class="backdrop" role="img" aria-label="Faded photo of a garden path beside a studio with plants and a white picket fence"></div>

    <svg class="artwork" width="960" height="1200" viewBox="0 0 960 1200">
      <defs>
        <linearGradient id="studio-photo" x1="0" y1="0" x2="1" y2="1">
          <stop offset="0" stop-color="#e4e0da"/>
          <stop offset="0.45" stop-color="#cfc7bb"/>
          <stop offset="0.75" stop-color="#8a7f70"/>
          <stop offset="1" stop-color="#3a3836"/>
        </linearGradient>
        <mask id="taupe-cut">
          <rect width="960" height="1200" fill="#fff"/>
          <circle cx="470" cy="462" r="250" fill="#000"/>
        </mask>
        <mask id="teal-cut">
          <rect width="960" height="1200" fill="#fff"/>
          <circle cx="490" cy="430" r="245" fill="#000"/>
        </mask>
      </defs>
      <circle class="ring-soft" cx="504" cy="452" r="262" fill="var(--taupe)" mask="url(#taupe-cut)"/>
      <circle class="ring-accent" cx="450" cy="452" r="264" fill="var(--teal)" mask="url(#teal-cut)"/>
      <circle class="workshop-photo" cx="476" cy="445" r="232" fill="url(#studio-photo)" role="img" aria-label="Photo of yoga mats, cork blocks and patterned bolsters laid out in a studio"/>
    </svg>

    <h1 class="title">
      <span class="line-one">YOGA &amp; PILATES</span>
      <span class="line-two">Workshop, Ashford</span>
    </h1>

    <section class="details">
      <p class="date">Saturday 24<sup>th</sup> March 2018</p>
      <p class="time">10.00am - 4.00pm</p>
      <p class="venue">Corewell Stretch &amp; Flow<br>18 Larch Street Ashford</p>
      <p class="investment-label">INVESTMENT</p>
      <p class="price">$120.00<br>$100.00 concession</p>
      <p class="booking">Book early&nbsp; Places are limited.</p>
    </section>

    <div class="brand">
      <span class="brand-dot"></span>
      <span class="brand-name">Corewell Stretch &amp; Flow</span>
    </div>
    <p class="tagline">move well, live well</p>
  </main>
</body>
</html>
```